New Business Card for Web Design/Internet Marketing Company

Looking for a great looking new business card. We are a 10 year old web design, internet marketing and website management company that works mostly with small businesses.

Our new card needs to better match the colors and style of our website, be bold, extremely usable and slightly edgy.

Target Market(s)

Small/Medium businesses that have websites

Industry/Entity Type

Internet

Requirements
Must have
• Front and back design, full color, rounded corners please

Must use the colors/style of our website (JPG provided)

INFO FOR CARDS (as readable as possible please)
Mark Lenner
President/CEO
mark@trelvanmedia.example
Phone: 520-381-7459
Toll Free: 866-381-7459
Address: 4315 W. Calloway Ave. Ste. 140, Tucson, AZ 85792

THINGS I WANT TO PROMOTE (if there is room):
1. Our Website - www.trelvanmedia.example

2. Social Media
Twitter: @trelvanmedia
Facebook: www.facebook.com/trelvanmedia

3. Our Services
Web Design
Internet Marketing
Website Management

```html
<!DOCTYPE html>
<html lang="en">
<head>
<meta charset="utf-8">
<title>Trelvan Media – Business Card</title>
<link rel="stylesheet" href="https://fonts.googleapis.com/css2?family=Open+Sans:wght@400;600;700&display=swap">
<style>
  :root {
    --orange: #f3862f;
    --blue: #1b93cf;
    --ink: #555759;
    --ink-dark: #3d3f41;
    --paper: #ffffff;
    --backdrop: #e9e6e2;
  }
  * { box-sizing: border-box; margin: 0; padding: 0; }
  html, body {
    width: 1200px; height: 758px; overflow: hidden;
    background: var(--backdrop);
    font-family: "Open Sans", Arial, sans-serif;
  }
  .canvas { position: relative; width: 1200px; height: 758px; }
  .card {
    position: absolute; top: 229px;
    width: 520px; height: 300px;
    border-radius: 26px; overflow: hidden;
    box-shadow: 0 6px 18px rgba(0,0,0,.18);
  }

  /* Front */
  .card-front { left: 50px; background: var(--paper); }
  .front-band {
    position: absolute; left: 0; bottom: 0; width: 100%; height: 110px;
  }
  .brand {
    position: absolute; left: 36px; top: 36px;
    display: flex; align-items: center; gap: 12px;
  }
  .brand-dot {
    width: 44px; height: 44px; border-radius: 50%;
    background: var(--blue); flex: none;
  }
  .brand-name {
    font-size: 30px; font-weight: 700; color: var(--orange); line-height: 1;
    white-space: nowrap;
  }
  .tagline {
    position: absolute; left: 92px; top: 86px;
    font-size: 13px; color: var(--ink); white-space: nowrap;
  }
  .person {
    position: absolute; right: 40px; top: 34px; text-align: right;
  }
  .person-name { font-size: 19px; font-weight: 700; color: var(--ink-dark); white-space: nowrap; }
  .person-title { font-size: 14px; color: var(--ink); }
  .contact-list {
    position: absolute; left: 36px; top: 142px; list-style: none;
  }
  .contact-list li {
    display: flex; align-items: center; gap: 8px;
    font-size: 13.5px; color: var(--ink); line-height: 20px; white-space: nowrap;
  }
  .contact-list svg { width: 12px; height: 12px; fill: var(--ink-dark); flex: none; }
  .corner-mark {
    position: absolute; right: 34px; top: 158px;
    font-size: 24px; font-weight: 700; color: var(--orange);
  }
  .address {
    position: absolute; left: 36px; bottom: 18px;
    font-size: 14px; color: var(--paper); font-weight: 600; white-space: nowrap;
  }

  /* Back */
  .card-back {
    left: 630px; background: var(--orange); color: var(--paper);
    text-align: center;
  }
  .back-brand {
    margin-top: 50px;
    display: flex; align-items: center; justify-content: center; gap: 16px;
  }
  .back-brand .brand-dot { width: 58px; height: 58px; background: var(--paper); }
  .back-brand .brand-name { color: var(--paper); font-size: 48px; }
  .services-title { margin-top: 30px; font-size: 24px; font-weight: 700; }
  .services { font-size: 19px; line-height: 25px; }
  .social {
    margin-top: 14px; display: flex; justify-content: center; gap: 26px;
    font-size: 13px;
  }
  .social span { display: flex; align-items: center; gap: 6px; }
  .social i {
    display: inline-block; width: 12px; height: 12px; background: var(--blue);
  }
</style>
</head>
<body>
<main class="canvas">

  <section class="card card-front" aria-label="Business card front">
    <svg class="front-band" viewBox="0 0 520 110" preserveAspectRatio="none" aria-hidden="true">
      <path d="M0 72 L430 44 Q520 38 520 0 L520 110 L0 110 Z" fill="var(--orange)"/>
    </svg>

    <div class="brand">
      <span class="brand-dot"></span>
      <span class="brand-name">Trelvan Media</span>
    </div>
    <p class="tagline">Sites that work for you</p>

    <div class="person">
      <p class="person-name">Mark Lenner</p>
      <p class="person-title">President/CEO</p>
    </div>

    <ul class="contact-list">
      <li><svg viewBox="0 0 12 12"><path d="M3 1 L5 3.5 L4 5 Q5 7 7 8 L8.5 7 L11 9 L9.5 11 Q2 10 1 2.5 Z"/></svg>866-381-7459</li>
      <li><svg viewBox="0 0 12 12"><path d="M3 1 L5 3.5 L4 5 Q5 7 7 8 L8.5 7 L11 9 L9.5 11 Q2 10 1 2.5 Z"/></svg>520-381-7459</li>
      <li><svg viewBox="0 0 12 12"><path d="M1 3 H11 V10 H1 Z M1 3 L6 7 L11 3" fill="none" stroke="var(--ink-dark)" stroke-width="1.4"/></svg>mark@trelvanmedia.example</li>
      <li><svg viewBox="0 0 12 12"><circle cx="6" cy="6" r="5"/></svg>www.trelvanmedia.example</li>
    </ul>

    <span class="corner-mark">Trelvan</span>

    <p class="address">4315 W. Calloway Ave. Ste. 140, Tucson, AZ 85792</p>
  </section>

  <section class="card card-back" aria-label="Business card back">
    <div class="back-brand">
      <span class="brand-dot"></span>
      <span class="brand-name">Trelvan</span>
    </div>
    <h2 class="services-title">Our Services</h2>
    <p class="services">• Web Design • Internet Marketing<br>• Website Management</p>
    <div class="social">
      <span><i></i>@trelvanmedia</span>
      <span><i></i>trelvanmedia</span>
    </div>
  </section>

</main>
</body>
</html>
```